Business Card for a mobile physiotherapy company

I need a layout for a business card for a mobile physiotherapy company.
Slogan is "Mobile Physiotherapy - Your Road To Recovery"
Phone number is 867-555-0142
Email VardenTherapy@postnest.ca (subject to change with website)
Website www.VardenTherapy.ca
My name and credentials: Luke Varden Luke Varden, BSc(kin), MPT, CAFCI, IMS
Information maybe included: Direct Billing, Services including Physiotherapy, IMS, acupuncture
Maybe include facebook and instagram logos
One side with the logo clean and sharp
Other side with details, try not to look too busy, keep everything concise

```html
<!DOCTYPE html>
<html lang="en">
<head>
<meta charset="utf-8">
<title>Varden Therapy – Business Card</title>
<link rel="stylesheet" href="https://fonts.googleapis.com/css2?family=Gelasio:wght@400;700&family=Roboto:ital,wght@0,400;1,400&display=swap">
<style>
  :root {
    --navy: #2c4a72;
    --green: #0d4f43;
    --white: #ffffff;
    --ink: #4a4a4a;
    --page: #eceae6;
    --serif: "Gelasio", "Palatino Linotype", Georgia, serif;
    --sans: "Roboto", Arial, sans-serif;
  }
  * { box-sizing: border-box; margin: 0; padding: 0; }
  html, body { width: 1125px; height: 1200px; overflow: hidden; }
  body { background: var(--page); position: relative; font-family: var(--serif); }

  .card {
    position: absolute;
    left: 171px;
    width: 800px;
    height: 456px;
    background: var(--white);
    overflow: hidden;
    box-shadow: 0 4px 10px rgba(0,0,0,0.18);
  }
  .card--front { top: 106px; }
  .card--back { top: 622px; }

  /* Front */
  .front__band {
    position: absolute; left: 0; top: 0; width: 100%; height: 258px;
    background: var(--navy);
  }
  .holder {
    position: absolute; right: 40px; top: 30px;
    text-align: right; color: var(--white);
  }
  .holder__name { font-size: 29px; font-weight: 700; letter-spacing: 0.5px; line-height: 1.1; }
  .holder__credentials,
  .holder__note { font-size: 19px; line-height: 1.35; }

  .contact {
    position: absolute; left: 62px; top: 328px;
    list-style: none; color: var(--ink); font-size: 19px;
  }
  .contact__item { display: flex; align-items: center; height: 25px; }
  .contact__icon { width: 16px; height: 16px; margin-right: 12px; fill: var(--navy); flex: none; }

  /* Company name set as plain text */
  .company {
    font-family: var(--serif);
    font-weight: 700;
    color: var(--green);
    line-height: 1;
    white-space: nowrap;
  }
  .company--front { position: absolute; right: 56px; top: 352px; font-size: 34px; }
  .company--back { position: absolute; left: 0; right: 0; top: 262px; text-align: center; font-size: 46px; }

  /* Back */
  .social { position: absolute; right: 48px; top: 40px; display: flex; gap: 4px; }
  .social__dot { width: 37px; height: 37px; border-radius: 50%; background: var(--navy); }

  .tagline {
    position: absolute; left: 0; right: 0; top: 376px;
    text-align: center; font-family: var(--sans);
  }
  .tagline__slogan { font-style: italic; color: var(--ink); font-size: 19px; line-height: 1.4; }
  .tagline__services { color: var(--green); font-size: 19px; line-height: 1.5; }
  .tagline__sep { color: var(--navy); padding: 0 2px; }
</style>
</head>
<body>

  <section class="card card--front" aria-label="Business card, front">
    <div class="front__band"></div>
    <div class="holder">
      <p class="holder__name">LUKE VARDEN</p>
      <p class="holder__credentials">BSc(kin), MPT, CAFCI, IMS</p>
      <p class="holder__note">Direct Billing</p>
    </div>

    <ul class="contact">
      <li class="contact__item">
        <svg class="contact__icon" viewBox="0 0 24 24" aria-hidden="true"><path d="M6.6 10.8a15.1 15.1 0 0 0 6.6 6.6l2.2-2.2a1 1 0 0 1 1-.25 11.4 11.4 0 0 0 3.6.57 1 1 0 0 1 1 1V20a1 1 0 0 1-1 1A17 17 0 0 1 3 4a1 1 0 0 1 1-1h3.5a1 1 0 0 1 1 1c0 1.25.2 2.45.57 3.6a1 1 0 0 1-.25 1z"/></svg>
        867-555-0142
      </li>
      <li class="contact__item">
        <svg class="contact__icon" viewBox="0 0 24 24" aria-hidden="true"><path d="M2 5h20v14H2z M4 7v.5l8 5.5 8-5.5V7l-8 5.5z" fill-rule="evenodd"/></svg>
        VardenTherapy@postnest.ca
      </li>
      <li class="contact__item">
        <svg class="contact__icon" viewBox="0 0 24 24" aria-hidden="true"><circle cx="12" cy="12" r="10"/><path d="M2 12h20M12 2c3 3 3 17 0 20M12 2c-3 3-3 17 0 20" stroke="#fff" stroke-width="1.5" fill="none"/></svg>
        www.VardenTherapy.ca
      </li>
    </ul>

    <p class="company company--front">Varden Therapy</p>
  </section>

  <section class="card card--back" aria-label="Business card, back">
    <div class="social" aria-label="Social media">
      <span class="social__dot"></span>
      <span class="social__dot"></span>
    </div>

    <p class="company company--back">Varden Therapy</p>

    <div class="tagline">
      <p class="tagline__slogan">Mobile Physiotherapy - Your Road To Recovery</p>
      <p class="tagline__services">Physiotherapy<span class="tagline__sep">•</span>IMS<span class="tagline__sep">•</span>Acupuncture</p>
    </div>
  </section>

</body>
</html>
```